Tech company needs a brochure design

Hi there.

We have written the text for a 4 page brochure, and this needs laying out.

We are in the process of rebranding, and have a new logo, but haven't yet established a colour pallete or design style.

Our current preference is for simple and bold. An example is the current website holding page is marvaxen.io

Colour pallet should pull from the logo for primary colours, but we're open to secondary colours.

The layout in the document is not set in stone, but should be used as a guideline.

The final text is almost ready (we're polishing the phrasing), but it will be almost identical in the number of words and layout.

Target Market(s)

Typically, they are companies that operate in highly regulated industries, such as Financial Services, Telecoms or Healthcare, are data-centric and need to adhere to regulations such as GDPR. Or, data-sensitive, such as Legal, Accountancy or even Retail, where a breach of the network would give access to highly sensitive information.

Regulations and compliance requirements affect the systems they have in place, particularly when it comes to managing and securing data.

All of this impacts the IT infrastructure that is needed, and Marvaxen can provide a seamless network that allows for all the regulations and doesn’t affect the working environment.

Marvaxen sells into these environments at a senior level – IT Director, CIO, CTO.

Industry/Entity Type

Cyber Security

Font styles to use
Sans Serif
Other font styles liked:
• Nexa

Requirements
Must have
• 4 pages in landscape
Clean design
Be appropriate for corporate/business environments but still have vitality
use attached logo for colours - Gray is #2f2f2f
Nice to have
• Can be white or dark based
Should not have
• Not Fussy
Icons that don’t have any relevance

```html
<!DOCTYPE html>
<html lang="en">
<head>
<meta charset="utf-8">
<title>Marvaxen brochure</title>
<link rel="stylesheet" href="https://fonts.googleapis.com/css2?family=Montserrat:wght@300;400;500;600;700&display=swap">
<style>
:root{
  --stage:#e4e4e4;
  --charcoal:#2f2f2f;
  --paper:#ececec;
  --red:#c62a22;
  --orange:#e2601c;
  --ink:#2b2b2b;
  --white:#ffffff;
  --muted:#cfcfcf;
  --plane-red:#efc2b8;
  --plane-white:#fbfbfb;
  --plane-grey:#d9d9d9;
}
*{box-sizing:border-box;margin:0;padding:0}
html,body{width:1200px;height:2361px;overflow:hidden}
body{background:var(--stage);font-family:"Montserrat",sans-serif;position:relative;color:var(--white)}

.page{position:absolute;overflow:hidden;box-shadow:0 14px 30px rgba(0,0,0,.18)}
.spread{position:absolute;left:20px;width:1160px;height:410px;display:flex;box-shadow:0 14px 30px rgba(0,0,0,.18)}
.spread .page{position:relative;box-shadow:none;width:580px;height:410px}

/* cover */
.cover{background:var(--paper)}
.cover--large{left:150px;top:140px;width:900px;height:636px;font-size:15.5px}
.cover--small{font-size:10px}
.cover-art{position:absolute;inset:0;width:100%;height:100%}
.brand-name{position:absolute;left:7.5%;top:17%;font-weight:600;font-size:2.9em;color:var(--white);letter-spacing:-.01em}
.cover-message{position:absolute;right:6%;top:46%;text-align:right;color:var(--ink)}
.cover-tagline{font-weight:300;font-size:1.45em;line-height:1.25;margin-bottom:.55em}
.cover-slogan{font-weight:700;font-size:1.95em;line-height:1.2;text-transform:uppercase}

/* back cover */
.back{background:var(--charcoal);padding:24px 30px 0 30px;font-size:7px;line-height:1.45}
.section-title{color:var(--orange);font-weight:600;text-transform:uppercase;font-size:8.6px;margin-bottom:3px;padding-left:7px;border-left:2px solid var(--red)}
.back p{color:var(--muted);margin-bottom:4px}
.back .block{margin-bottom:7px}
.ways-box{background:#e9e9e9;border-radius:8px;color:var(--ink);padding:9px 12px;display:grid;grid-template-columns:1.1fr 1fr 1fr;gap:10px;margin:6px 0 9px}
.ways-intro{grid-column:1/-1;font-size:10px;font-weight:400}
.way-title{font-weight:600;font-size:6.8px;margin-bottom:2px}
.way-title span{color:var(--orange)}
.ways-box p{color:#666;margin:0}
.contact-band{position:absolute;left:30px;right:30px;bottom:22px;height:70px;display:flex;border-radius:6px;overflow:hidden}
.contact-cta{width:36%;background:var(--red);font-size:9.4px;line-height:1.35;padding:14px 12px;position:relative}
.contact-cta::after{content:"";position:absolute;right:-14px;top:0;border-left:14px solid var(--red);border-top:35px solid transparent;border-bottom:35px solid transparent;z-index:2}
.contact-details{flex:1;background:linear-gradient(90deg,#d8401e,var(--orange));padding:14px 12px 0 28px;font-size:6.4px;line-height:1.6}
.contact-details strong{font-size:9.5px;font-weight:600;display:block;margin-bottom:2px}

/* inside spread */
.inside{background:var(--charcoal);font-size:7.6px;line-height:1.55}
.inside-left{padding:34px 34px 0 34px}
.feature-title{color:var(--orange);font-weight:500;font-size:14px;line-height:1.15;padding-left:8px;border-left:3px solid var(--red);margin-bottom:10px}
.inside p{color:var(--muted);margin-bottom:7px}
.stats-band{position:absolute;left:34px;right:34px;bottom:26px;height:92px;border-radius:10px;background:linear-gradient(90deg,var(--red),var(--orange));display:flex;justify-content:space-around;align-items:flex-end;padding-bottom:12px}
.stat{text-align:center;width:30%;position:relative}
.stat-icon{width:34px;height:34px;border-radius:50%;background:#f1f1f1;margin:-22px auto 6px;display:flex;align-items:center;justify-content:center;border:2px solid rgba(255,255,255,.6)}
.stat-value{font-weight:700;font-size:26px;line-height:1}
.stat-label{font-size:7px;line-height:1.3;margin-top:3px}
.inside-right{display:flex}
.inside-right .copy{width:68%;padding:28px 20px 0 28px}
.inside-right p{font-size:7.2px}
.sub-title{color:var(--orange);font-weight:500;font-size:9px;padding-left:6px;border-left:2px solid var(--red);margin:4px 0 4px}
.photo-slot{width:32%;background:linear-gradient(160deg,#f5f5f5 0%,#f1d2c2 45%,#e0683a 75%,#c8401f 100%)}
</style>
</head>
<body>

<!-- Front cover -->
<section class="page cover cover--large">
  <svg class="cover-art" viewBox="0 0 1000 707" preserveAspectRatio="none">
    <defs>
      <linearGradient id="paperLarge" x1="0" y1="0" x2="1" y2="1"><stop offset="0" stop-color="#f0f0f0"/><stop offset="1" stop-color="#c6c6c6"/></linearGradient>
      <linearGradient id="sweepLarge" x1="0" y1="1" x2="1" y2="0"><stop offset="0" stop-color="#c02520"/><stop offset="1" stop-color="#e8651c"/></linearGradient>
      <linearGradient id="flockLarge" x1="0" y1="0" x2="0" y2="1"><stop offset="0" stop-color="var(--plane-white)"/><stop offset="1" stop-color="var(--plane-grey)"/></linearGradient>
      <linearGradient id="leadLarge" x1="0" y1="0" x2="0" y2="1"><stop offset="0" stop-color="var(--plane-red)"/><stop offset="1" stop-color="#f3e4e0"/></linearGradient>
    </defs>
    <rect width="1000" height="707" fill="url(#paperLarge)"/>
    <g role="img" aria-label="Illustration: a flock of white paper planes flying upward, led by a single red paper plane trailing a dashed flight path">
      <rect x="200" y="110" width="360" height="597" fill="url(#flockLarge)"/>
      <rect x="560" y="110" width="170" height="250" fill="url(#leadLarge)"/>
    </g>
    <path d="M0 0 H830 Q300 140 210 707 H0 Z" fill="var(--charcoal)"/>
    <path d="M830 0 Q300 140 210 707 L238 707 Q350 175 830 0 Z" fill="url(#sweepLarge)"/>
  </svg>
  <div class="brand-name">Marvaxen</div>
  <div class="cover-message">
    <p class="cover-tagline">Propelling clients<br>through the journey to efficiency</p>
    <p class="cover-slogan">Change your thinking<br>Change your approach<br>Reap the rewards</p>
  </div>
</section>

<!-- Outer spread: back cover + front cover -->
<div class="spread" style="top:1030px">
  <section class="page back">
    <div class="block">
      <h2 class="section-title">Structuring your business in the right way</h2>
      <p>Budgets are tight, technology and security teams need to do more with less, whilst the business requires an ever-increasing array of new technologies to stay ahead of the competition. Marvaxen provides a holistic wrapper around people, processes and technology to create a more efficient organisation that operates and runs more effectively, enabling you to deliver products and services to market faster while enhancing the customer experience.</p>
    </div>
    <div class="block">
      <h2 class="section-title">Propelling your technology journey</h2>
      <p>Every organisation is different. Requirements differ, structures contrast and objectives vary. One size does not fit all and an all encompassing view is essential to start the journey from the correct point and achieve the desired outcome.</p>
      <p>At Marvaxen, we consider our client's entire eco-system. By understanding the nuances of compliance obligations, employee practice, technical complexities and process requirements, we redefine the problem to build the solution that will drive your business forward.</p>
    </div>
    <div class="ways-box">
      <p class="ways-intro">There are several ways we work with our clients.</p>
      <div><p class="way-title">Manage the journey <span>For You</span></p><p>Marvaxen takes control and full responsibility, so you don't have to worry. We manage the risk. You gain the results and the desired outcome.</p></div>
      <div><p class="way-title">Go on the journey <span>With You</span></p><p>We work in partnership with you, enhancing your existing team and upskilling your capabilities along the way.</p></div>
      <div><p class="way-title">The journey is taken <span>By You</span></p><p>Marvaxen provide you with the right tools to make the journey yourself.</p></div>
    </div>
    <div class="block">
      <h2 class="section-title">Your peace of mind is essential</h2>
      <p>Building trust and working in partnership with our clients is important to us. Marvaxen follows a framework-led, principle-based approach with a unique methodology, and has extensive technical expertise across the leading technologies in the market.</p>
    </div>
    <div class="contact-band">
      <div class="contact-cta">Contact us today to talk about setting your business on the journey to efficiency</div>
      <div class="contact-details">
        <strong>Marvaxen</strong>
        E. info@marvaxen.io &nbsp;|&nbsp; W. marvaxen.io &nbsp;|&nbsp; T. +44 (0)1632 960418<br>
        Unit 5 | Orchard Court | Kingsway | Halden | Westshire | HD4 2LM
      </div>
    </div>
  </section>

  <section class="page cover cover--small">
    <svg class="cover-art" viewBox="0 0 1000 707" preserveAspectRatio="none">
      <defs>
        <linearGradient id="paperSmall" x1="0" y1="0" x2="1" y2="1"><stop offset="0" stop-color="#f0f0f0"/><stop offset="1" stop-color="#c6c6c6"/></linearGradient>
        <linearGradient id="sweepSmall" x1="0" y1="1" x2="1" y2="0"><stop offset="0" stop-color="#c02520"/><stop offset="1" stop-color="#e8651c"/></linearGradient>
        <linearGradient id="flockSmall" x1="0" y1="0" x2="0" y2="1"><stop offset="0" stop-color="var(--plane-white)"/><stop offset="1" stop-color="var(--plane-grey)"/></linearGradient>
        <linearGradient id="leadSmall" x1="0" y1="0" x2="0" y2="1"><stop offset="0" stop-color="var(--plane-red)"/><stop offset="1" stop-color="#f3e4e0"/></linearGradient>
      </defs>
      <rect width="1000" height="707" fill="url(#paperSmall)"/>
      <g role="img" aria-label="Illustration: a flock of white paper planes flying upward, led by a single red paper plane trailing a dashed flight path">
        <rect x="200" y="110" width="360" height="597" fill="url(#flockSmall)"/>
        <rect x="560" y="110" width="170" height="250" fill="url(#leadSmall)"/>
      </g>
      <path d="M0 0 H830 Q300 140 210 707 H0 Z" fill="var(--charcoal)"/>
      <path d="M830 0 Q300 140 210 707 L238 707 Q350 175 830 0 Z" fill="url(#sweepSmall)"/>
    </svg>
    <div class="brand-name">Marvaxen</div>
    <div class="cover-message">
      <p class="cover-tagline">Propelling clients<br>through the journey to efficiency</p>
      <p class="cover-slogan">Change your thinking<br>Change your approach<br>Reap the rewards</p>
    </div>
  </section>
</div>

<!-- Inside spread -->
<div class="spread" style="top:1740px">
  <section class="page inside inside-left">
    <h2 class="feature-title">A Different Provider<br>A Different Type of Business Solution</h2>
    <p>We are Marvaxen. We have been propelling companies on the journey to automation and efficiency since 2005.</p>
    <p>Our expertise lies in modernising, automating and securing complex technical environments. By balancing the requirements of compliance with the realities of technology, process and people, we establish a clean, compliant and secure business setting that is robust, easy to run, straightforward to maintain and effortless to adapt and scale.</p>
    <p>We are different from others in our approach. In listening to our clients and applying Marvaxen's unique methodology, we look at the whole environment and challenge the existing way of doing things, delivering comprehensive and secure solutions.</p>
    <p>In providing our clients with an efficient, secure and compliant environment, productivity improvements are recognised, whilst costs and risk are reduced and the customer experience is delivered to establish competitive advantage in the market.</p>
    <div class="stats-band">
      <div class="stat">
        <div class="stat-icon"><svg width="18" height="18" viewBox="0 0 24 24" fill="none" stroke="#444" stroke-width="2"><circle cx="12" cy="12" r="3.5"/><circle cx="12" cy="12" r="8"/></svg></div>
        <div class="stat-value">84%</div><div class="stat-label">More efficient IT<br>operations</div>
      </div>
      <div class="stat">
        <div class="stat-icon"><svg width="18" height="18" viewBox="0 0 24 24" fill="none" stroke="#444" stroke-width="2"><circle cx="12" cy="13" r="8"/><path d="M12 13V9M10 3h4"/></svg></div>
        <div class="stat-value">92%</div><div class="stat-label">Increase in speed of<br>execution &amp; delivery</div>
      </div>
      <div class="stat">
        <div class="stat-icon"><svg width="18" height="18" viewBox="0 0 24 24" fill="none" stroke="#444" stroke-width="2"><circle cx="12" cy="12" r="9"/><path d="M14.5 8.5a2.5 2.5 0 0 0-5 .5v7M8 12.5h5M8 16h7.5"/></svg></div>
        <div class="stat-value">60%</div><div class="stat-label">Reduction in costs<br>to the business</div>
      </div>
    </div>
  </section>

  <section class="page inside inside-right">
    <div class="copy">
      <h3 class="sub-title">The Changing Landscape</h3>
      <p>Today's fast-paced business environment is a complex world. Technology and the way that people consume information is evolving at speed and continuously changing. Most organisations have evolved over time and often consist of legacy technologies added incrementally, making them hard to adapt and time-consuming to manage. This operational complexity, driven by the need to adhere to current compliance and ever-changing working practices, is only increasing the pressure on already strained resources.</p>
      <p>These are the environments where Marvaxen excels. We streamline and automate the IT estate, rationalising and securing technology, processes and systems. We propel our clients towards the digital, secure and compliant environment needed for business success.</p>
      <h3 class="sub-title">Digital Efficiency</h3>
      <p>An efficient digital environment will establish competitive advantage in this interconnected world. People, process and technology need to be streamlined and Marvaxen are experts in unifying and refining this environment. By merging our unique methodology with market-leading technologies, Marvaxen will deliver you digital efficiency that drives your competitive advantage.</p>
      <h3 class="sub-title">Governance, Risk &amp; Compliance</h3>
      <p>Data is often the lifeblood of companies and regulations abound. Making sense of this environment and protecting sensitive information, whether that's client or corporate data, is fundamental. Marvaxen can identify your risk profile and pinpoint areas of concern, guiding you in establishing good governance around policy, procedures and technology use.</p>
    </div>
    <div class="photo-slot" role="img" aria-label="Photo of a businessman holding a tablet with floating charts, washed in orange tones over a city skyline"></div>
  </section>
</div>

</body>
</html>
```